Home Remodeling company needs a business card design

we need a business card design for home remodeling company in hamilton county, indiana USA. we offers a wide range of construction services including whole house renovations, Design and Build Basements and Kitchen and Bathroom Remodeling . we would like to see designs for both site of business card that use the same color of the company logo and also including all information below :
1- Karim Feltous CEO / General Contractor
2- all company contacts Telephone numbers ( 1-888-DULOM-47 ) ( 317-555-0193) email address ( info@dulomhome.com) website ( www.dulomhome.com ) and social media logos (Facebook- twitter- google plus )
3- company logo
4- licensed . insured . bonded

```html
<!DOCTYPE html>
<html lang="en">
<head>
<meta charset="utf-8">
<title>Dulom Business Card</title>
<link href="https://fonts.googleapis.com/css2?family=Open+Sans:wght@400;600;700&display=swap" rel="stylesheet">
<style>
  :root {
    --backdrop: #000000;
    --card-light: #f3f3f3;
    --brand-red: #c6323b;
    --accent-red: #c8202c;
    --ink: #1e1e1e;
    --logo-ink: #333333;
    --white: #ffffff;
  }
  * { margin: 0; padding: 0; box-sizing: border-box; }
  html, body {
    width: 1200px; height: 900px; overflow: hidden;
    background: var(--backdrop);
    font-family: "Open Sans", Arial, sans-serif;
  }
  .canvas { position: relative; width: 1200px; height: 900px; }

  .card { position: absolute; top: 200px; width: 310px; height: 502px; }
  .card-front {
    left: 274px; background: var(--card-light);
    border-radius: 50px 0 50px 0;
  }
  .card-back {
    left: 637px; background: var(--brand-red);
    border-radius: 0 58px 0 58px;
  }

  .wordmark {
    position: absolute; display: flex; align-items: center; gap: 8px;
    font-weight: 700; letter-spacing: 1px; line-height: 1;
  }
  .wordmark .mark-square { width: 12px; height: 12px; display: block; }
  .card-front .wordmark { left: 38px; top: 58px; font-size: 40px; color: var(--logo-ink); }
  .card-front .wordmark .mark-square { background: var(--accent-red); }
  .card-back .wordmark { left: 38px; top: 360px; font-size: 40px; color: var(--white); }
  .card-back .wordmark .mark-square { background: var(--white); }

  .holder { position: absolute; left: 23px; top: 287px; }
  .holder-name { font-size: 16px; font-weight: 700; color: var(--accent-red); line-height: 22px; }
  .holder-title { font-size: 13.5px; color: var(--ink); line-height: 20px; }

  .contacts { position: absolute; left: 27px; top: 354px; list-style: none; }
  .contacts li {
    display: flex; align-items: center; gap: 6px;
    font-size: 13.5px; color: var(--ink); height: 21px;
  }
  .contacts svg { width: 11px; height: 11px; fill: var(--accent-red); flex: none; }

  .social { position: absolute; left: 27px; top: 451px; display: flex; gap: 8px; }
  .social span { width: 16px; height: 16px; border-radius: 50%; background: var(--ink); display: block; }

  .credentials {
    position: absolute; left: 42px; top: 426px;
    font-size: 15px; font-weight: 600; color: var(--white); white-space: nowrap;
  }
</style>
</head>
<body>
<main class="canvas">
  <section class="card card-front" aria-label="Card front">
    <div class="wordmark"><span class="mark-square"></span>DULOM</div>

    <div class="holder">
      <p class="holder-name">Karim Feltous</p>
      <p class="holder-title">CEO / General Contractor</p>
    </div>

    <ul class="contacts">
      <li>
        <svg viewBox="0 0 24 24" aria-hidden="true"><path d="M6.6 10.8a15.1 15.1 0 0 0 6.6 6.6l2.2-2.2a1 1 0 0 1 1-.25 11.4 11.4 0 0 0 3.6.57 1 1 0 0 1 1 1V20a1 1 0 0 1-1 1A17 17 0 0 1 3 4a1 1 0 0 1 1-1h3.5a1 1 0 0 1 1 1c0 1.25.2 2.45.57 3.57a1 1 0 0 1-.25 1z"/></svg>
        1-888-DULOM-47
      </li>
      <li>
        <svg viewBox="0 0 24 24" aria-hidden="true"><path d="M6.6 10.8a15.1 15.1 0 0 0 6.6 6.6l2.2-2.2a1 1 0 0 1 1-.25 11.4 11.4 0 0 0 3.6.57 1 1 0 0 1 1 1V20a1 1 0 0 1-1 1A17 17 0 0 1 3 4a1 1 0 0 1 1-1h3.5a1 1 0 0 1 1 1c0 1.25.2 2.45.57 3.57a1 1 0 0 1-.25 1z"/></svg>
        317-555-0193
      </li>
      <li>
        <svg viewBox="0 0 24 24" aria-hidden="true"><path d="M2 5h20v14H2z M2 5l10 8 10-8" /><path d="M3 6l9 7 9-7v-.5H3z" fill="#f3f3f3"/></svg>
        info@dulomhome.com
      </li>
      <li>
        <svg viewBox="0 0 24 24" aria-hidden="true"><path d="M10.6 13.4a1 1 0 0 1 0-1.4l3.5-3.5a1 1 0 1 1 1.4 1.4L12 13.4a1 1 0 0 1-1.4 0zM8.5 20a4.5 4.5 0 0 1-3.2-7.7l2.1-2.1 1.4 1.4-2.1 2.1a2.5 2.5 0 0 0 3.5 3.5l2.1-2.1 1.4 1.4-2.1 2.1A4.5 4.5 0 0 1 8.5 20zm8.1-6.2-1.4-1.4 2.1-2.1a2.5 2.5 0 0 0-3.5-3.5l-2.1 2.1-1.4-1.4 2.1-2.1a4.5 4.5 0 0 1 6.4 6.4z"/></svg>
        www.dulomhome.com
      </li>
    </ul>

    <div class="social" aria-label="Social media links">
      <span></span><span></span><span></span>
    </div>
  </section>

  <section class="card card-back" aria-label="Card back">
    <div class="wordmark"><span class="mark-square"></span>DULOM</div>
    <p class="credentials">Licensed &bull; Insured &bull; Bonded</p>
  </section>
</main>
</body>
</html>
```